Android Payment Application UI Design

We require a UI/UX design for an existing Android card-based payment application.

We're looking to improve the look + feel of the existing app. What we're after:
- Colour palette options
- Fonts
- Icons

See attached document for existing screen types, icons, etc.

All resources provided must be royalty free.

It's to run on a specialised device, with 720 x 1280 pixel resolution, in portrait only (landscape not required).

Please provide mockup examples of the new screen layout applied to the existing screens in the document.

Target Market(s)

Retail business users

Font styles to use
Sans Serif

Colors

Designer to choose colors to be used in the design.

Requirements
Must have
• Looking for
• - modern design
• - simple colours, easy-to-read sans-serif fonts
• - cohesive, consistent design between screens

```html
<!DOCTYPE html>
<html lang="en">
<head>
<meta charset="utf-8">
<title>Test Connect – Authorised</title>
<link href="https://fonts.googleapis.com/css2?family=Nunito:wght@400;600;700;800&display=swap" rel="stylesheet">
<style>
  :root {
    --status-top: #1d4f86;
    --status-bottom: #2f6fae;
    --status-text: #ffffff;
    --header-bg: #ffffff;
    --header-rule: #e3e8ee;
    --icon-grey: #4a4f57;
    --brand-blue: #2a8fd0;
    --brand-grey: #8c929a;
    --heading-navy: #24263f;
    --body-top: #ffffff;
    --body-bottom: #6fc0ea;
    --tick-green: #22a52b;
    --ring-light: #f4f4f4;
    --ring-dark: #9a9a9a;
  }
  * { margin: 0; padding: 0; box-sizing: border-box; }
  html, body { width: 675px; height: 1200px; overflow: hidden; }
  body {
    font-family: "Nunito", "Helvetica Neue", Arial, sans-serif;
    background: var(--body-top);
  }
  .screen {
    position: relative;
    width: 675px;
    height: 1200px;
    background: linear-gradient(180deg, var(--body-top) 0%, var(--body-top) 22%, var(--body-bottom) 100%);
    overflow: hidden;
  }
  .status-bar {
    position: absolute; top: 0; left: 0; right: 0;
    height: 42px;
    background: linear-gradient(180deg, var(--status-top), var(--status-bottom));
    color: var(--status-text);
    font-size: 21px;
    font-weight: 600;
    display: flex; align-items: center;
    padding: 0 14px;
  }
  .status-carrier { display: flex; align-items: center; gap: 8px; }
  .signal-dots { display: flex; gap: 3px; }
  .signal-dots span { width: 9px; height: 9px; border-radius: 50%; background: var(--status-text); }
  .signal-dots span.empty { background: transparent; border: 1.5px solid var(--status-text); }
  .status-time { position: absolute; left: 0; right: 0; text-align: center; pointer-events: none; }
  .status-battery { margin-left: auto; display: flex; align-items: center; gap: 8px; }
  .app-header {
    position: absolute; top: 42px; left: 0; right: 0;
    height: 138px;
    background: var(--header-bg);
    border-bottom: 2px solid var(--header-rule);
    display: flex; align-items: center; justify-content: space-between;
    padding: 0 20px;
  }
  .brand {
    display: flex; align-items: center; gap: 14px;
    font-size: 50px; font-weight: 800;
    color: var(--brand-blue);
    letter-spacing: 1px;
  }
  .brand-dot { width: 40px; height: 40px; border-radius: 50%; background: var(--brand-blue); }
  .result-title, .result-status {
    position: absolute; left: 0; right: 0;
    text-align: center;
    color: var(--heading-navy);
    font-weight: 700;
    font-size: 46px;
    letter-spacing: 0.5px;
  }
  .result-title { top: 292px; }
  .result-status { top: 528px; }
  .confirm-button {
    position: absolute;
    left: 274px; top: 972px;
    width: 128px; height: 128px;
  }
</style>
</head>
<body>
<main class="screen">
  <div class="status-bar">
    <div class="status-carrier">
      <div class="signal-dots"><span></span><span></span><span></span><span></span><span class="empty"></span></div>
      <span>Carrier</span>
      <svg width="16" height="20" viewBox="0 0 16 20" aria-hidden="true"><path d="M2 1h8l5 5v13H2z" fill="none" stroke="#fff" stroke-width="2"/><rect x="5" y="9" width="7" height="7" fill="#fff"/></svg>
    </div>
    <div class="status-time">11:49 AM</div>
    <div class="status-battery">
      <span>2%</span>
      <svg width="40" height="20" viewBox="0 0 40 20" aria-hidden="true"><rect x="1" y="2" width="33" height="16" rx="3" fill="none" stroke="#fff" stroke-width="2"/><rect x="35" y="7" width="3" height="6" fill="#fff"/><path d="M10 11h12l-3-4M22 9H10l3 4" fill="none" stroke="#fff" stroke-width="1.8"/></svg>
    </div>
  </div>

  <header class="app-header">
    <svg class="icon-database" width="26" height="34" viewBox="0 0 26 34" aria-label="Records">
      <ellipse cx="13" cy="5" rx="12" ry="4.5" fill="var(--icon-grey)"/>
      <path d="M1 9c0 3 5 5 12 5s12-2 12-5v6c0 3-5 5-12 5S1 18 1 15z" fill="var(--icon-grey)"/>
      <path d="M1 19c0 3 5 5 12 5s12-2 12-5v6c0 3-5 5-12 5S1 28 1 25z" fill="var(--icon-grey)"/>
    </svg>
    <div class="brand"><span class="brand-dot"></span>NOVA</div>
    <svg class="icon-menu" width="32" height="28" viewBox="0 0 32 28" aria-label="Menu">
      <rect x="0" y="2" width="5" height="5" fill="var(--icon-grey)"/><rect x="9" y="3" width="23" height="3" fill="var(--icon-grey)"/>
      <rect x="0" y="12" width="5" height="5" fill="var(--icon-grey)"/><rect x="9" y="13" width="23" height="3" fill="var(--icon-grey)"/>
      <rect x="0" y="22" width="5" height="5" fill="var(--icon-grey)"/><rect x="9" y="23" width="23" height="3" fill="var(--icon-grey)"/>
    </svg>
  </header>

  <h1 class="result-title">TEST CONNECT</h1>
  <p class="result-status">AUTHORISED</p>

  <svg class="confirm-button" viewBox="0 0 128 128" aria-label="Confirm">
    <defs>
      <linearGradient id="ring" x1="0" y1="0" x2="0" y2="1">
        <stop offset="0" stop-color="var(--ring-light)"/>
        <stop offset="1" stop-color="var(--ring-dark)"/>
      </linearGradient>
      <radialGradient id="core" cx="0.45" cy="0.35" r="0.7">
        <stop offset="0" stop-color="#5a5a5a"/>
        <stop offset="1" stop-color="#1a1a1a"/>
      </radialGradient>
    </defs>
    <circle cx="64" cy="64" r="62" fill="url(#ring)"/>
    <circle cx="64" cy="64" r="50" fill="url(#core)"/>
    <circle cx="64" cy="64" r="38" fill="var(--tick-green)"/>
    <path d="M44 65l14 14 28-30" fill="none" stroke="#fff" stroke-width="10" stroke-linecap="round" stroke-linejoin="round"/>
  </svg>
</main>
</body>
</html>
```